Laboratory and geotechnical service provider needs Word template

We require a new Word Template for our business. We are looking for a modern, business-like format. We typically generate reports such as management plans, business plans, method statements, technical reports. These reports cover generally between 5 and 30 pages, but sometimes up to 500 pages including the appendices.

Lab reports have their own formats and are not parts of this scope.

Target Market(s)

We report to Clients such as construction industry contractors, governmental departments and engineering consultants.

Industry/Entity Type

Technical Service

Colors

Designer to choose colors to be used in the design.

Requirements
Must have
• The report needs a fancy cover page with a title field, subtitle, project field, client name field, reference number field. Photo/graphics as background on cover. Second page needs a revision table for document control. Table of contents up to 2 levels. Appendices to be part of TOC. Report first page with custom headings for body text, titles, subtitles, headings 1, 2, 3, etc. Include a table with caption, figure with caption, bullet list, numbered list. Appendix page. Please use fonts consistently, choose a common, but professional, modern font.
Nice to have
• We traditionally use black and yellow as company colours. Please visit our company page www.brennixtesting.com.
Should not have
• The two attached word documents is what we use now for your information, we are looking for something better!

```html
<!DOCTYPE html>
<html lang="en">
<head>
<meta charset="utf-8">
<title>Identifying Stakeholders</title>
<link href="https://fonts.googleapis.com/css2?family=Anton&family=Arimo:wght@400;700&display=swap" rel="stylesheet">
<style>
  :root {
    --ink: #111111;
    --paper: #ffffff;
    --brand-yellow: #f9ec0b;
    --rule-yellow: #f7ea14;
    --photo-sky: #5f6675;
    --photo-mid: #4a4f58;
    --photo-ground: #3f5a3a;
  }
  html, body {
    margin: 0;
    padding: 0;
    overflow: hidden;
    background: var(--paper);
  }
  .page {
    position: relative;
    width: 927px;
    height: 1200px;
    background: var(--paper);
    color: var(--ink);
    font-family: "Arimo", Arial, sans-serif;
    overflow: hidden;
  }
  .section-title {
    position: absolute;
    left: 100px;
    top: 62px;
    margin: 0;
    font-family: "Anton", "Oswald", sans-serif;
    font-weight: 400;
    font-size: 60px;
    line-height: 70px;
    letter-spacing: 0.2px;
    color: var(--ink);
  }
  .title-underline {
    position: absolute;
    left: 101px;
    top: 139px;
    width: 417px;
    height: 5px;
    background: var(--rule-yellow);
  }
  .intro {
    position: absolute;
    left: 102px;
    top: 168px;
    width: 760px;
    margin: 0;
    font-size: 16.4px;
    line-height: 24px;
  }
  .site-photo {
    position: absolute;
    left: 105px;
    top: 225px;
    width: 746px;
    height: 781px;
    background: linear-gradient(180deg, var(--photo-sky) 0%, var(--photo-mid) 55%, var(--photo-ground) 100%);
  }
  .criteria-panel {
    position: absolute;
    left: 420px;
    top: 301px;
    width: 393px;
    height: 729px;
    background: var(--brand-yellow);
  }
  .criteria-list {
    position: absolute;
    left: 31px;
    top: 14px;
    width: 350px;
    margin: 0;
    padding: 0;
    list-style: none;
    font-size: 16.4px;
    line-height: 23.8px;
  }
  .panel-rule {
    position: absolute;
    left: 30px;
    top: 464px;
    width: 181px;
    height: 3px;
    background: var(--ink);
  }
  .panel-note {
    position: absolute;
    left: 29px;
    top: 485px;
    width: 350px;
    margin: 0;
    font-size: 16.4px;
    line-height: 23.8px;
  }
  .footer-rule {
    position: absolute;
    left: 108px;
    top: 1049px;
    width: 181px;
    height: 3px;
    background: var(--ink);
  }
  .register-note {
    position: absolute;
    left: 108px;
    top: 1063px;
    width: 700px;
    margin: 0;
    font-size: 16.4px;
    line-height: 24px;
  }
  .doc-number {
    position: absolute;
    right: 34px;
    top: 1145px;
    margin: 0;
    font-size: 11px;
    font-weight: 700;
  }
</style>
</head>
<body>
<div class="page">
  <h1 class="section-title">IDENTIFYING STAKEHOLDERS</h1>
  <div class="title-underline"></div>

  <p class="intro">As part of the project planning process, the project management team shall identity potential<br>stakeholders against the following criteria:</p>

  <div class="site-photo" role="img" aria-label="Drilling rig on a waterfront construction site with palm trees and city towers behind"></div>

  <div class="criteria-panel">
    <ul class="criteria-list">
      <li>• Will the person or their organization be<br>directly or indirectly affected by this<br>project?</li>
      <li>• Does the person or their organization<br>hold a position from which they can<br>influence the<br>project?</li>
      <li>• Does the person have an impact on the<br>project’s resources (material, personnel,<br>funding)?</li>
      <li>• Does the person or their organization<br>have any special skills or capabilities the<br>project will<br>require?</li>
      <li>• Does the person potentially benefit from<br>the project or are they in a position to<br>resist this<br>change?</li>
    </ul>
    <div class="panel-rule"></div>
    <p class="panel-note">Stakeholders may include BOTH internal<br>and external personnel or organisations.<br>Internal stakeholders might include the<br>project team, including contractors and<br>vendors, as well as<br>top management, resourcing directors,<br>accounting department members, and<br>others who want to see the project run<br>efficiently and profitably.</p>
  </div>

  <div class="footer-rule"></div>
  <p class="register-note">Once identified, all Stakeholders shall be recorded in the Stakeholder Management<br>Register. See Appendix A</p>

  <p class="doc-number">DOC. # BT-O78097-SMP</p>
</div>
</body>
</html>
```